Website for a new t-shirt company called bolddawnapperal.com

We are looking for a talented web designer to create a website that aligns with our brand's message and identity centered around the theme of "Bold Dawn." The website should be modern, clean, and visually appealing while also being user-friendly and easy to navigate.

We will be using the Big Commerce platform for our online store section, so the designer should have experience in designing websites on this platform.

We would like the website to have the following elements:

A color scheme that aligns with the brand's identity and message
A homepage that showcases our products and message, with clear calls-to-action for visitors to explore further
A blog section that highlights our brand's philosophy and offers advice and tips for people looking to make positive changes in their lives
An "About Us" section that introduces our brand and team and offers insight into our mission and values
A contact form that allows visitors to easily get in touch with us for inquiries or support
We are open to creative suggestions and ideas from the designer, but we would like the website to have a modern and minimalist aesthetic that resonates with our target audience of 20 to 40-year-olds.

```html
<!DOCTYPE html>
<html lang="en">
<head>
<meta charset="utf-8">
<title>Bold Dawn Apparel</title>
<link rel="stylesheet" href="https://fonts.googleapis.com/css2?family=Poppins:wght@300;400;500;600;700&display=swap">
<style>
:root{
  --ink:#1f1f1f;
  --muted:#6b6b6b;
  --card:#f3f3f3;
  --line:#d9d9d9;
  --black:#000;
  --white:#fff;
  --yellow:#f1c31a;
}
*{margin:0;padding:0;box-sizing:border-box}
html,body{width:1200px;height:4170px;overflow:hidden;background:var(--white)}
body{position:relative;font-family:'Poppins',sans-serif;color:var(--ink)}
.abs{position:absolute}
a{color:inherit;text-decoration:none}

/* header */
.search{left:97px;top:40px;width:195px;height:28px;border-bottom:1.5px solid var(--ink);font-size:9px;color:#444;padding-top:6px}
.search svg{position:absolute;right:4px;top:5px}
.brand{font-weight:500;font-size:42px;letter-spacing:1px;color:var(--ink)}
.header-brand{left:0;width:1200px;top:28px;text-align:center}
.header-icons{left:950px;top:44px;display:flex;gap:38px}
.ship{left:97px;top:130px;font-size:10.5px;font-weight:500}
.nav{left:390px;top:127px;display:flex;gap:38px;font-size:13.5px;font-weight:500}
.login{left:978px;top:110px;width:123px;height:57px;border:2.5px solid var(--ink);display:flex;align-items:center;justify-content:center;font-size:13px;font-weight:600}

/* hero */
.hero-photo{left:314px;top:207px;width:886px;height:585px;background:linear-gradient(100deg,#a78d6f 0%,#d8cfc4 40%,#eceae6 55%,#8f7558 80%,#3b4a34 100%)}
.hero-title{left:99px;top:295px;font-size:80px;line-height:100px;font-weight:400;color:var(--ink)}
.hero-btn{left:99px;top:645px;width:154px;height:57px;border:2.5px solid var(--ink);display:flex;align-items:center;justify-content:center;font-size:13.5px;font-weight:600;background:rgba(255,255,255,.0)}
.dot-btn{top:757px;width:26px;height:26px;border-radius:50%;border:1px solid var(--line);display:flex;align-items:center;justify-content:center}

/* products */
.section-title{left:0;width:1200px;text-align:center;font-size:30px;font-weight:600;letter-spacing:.3px}
.card{width:236px}
.card-img{height:225px;border-radius:6px;position:relative}
.card-fav{position:absolute;right:14px;top:16px;width:24px;height:24px;border-radius:50%;background:var(--white);display:flex;align-items:center;justify-content:center}
.card-row{display:flex;justify-content:space-between;margin-top:20px;padding-right:18px}
.card-name{font-size:18px;font-weight:600}
.card-price{font-size:15px;color:#333}
.card-desc{font-size:12.5px;color:#444;margin-top:4px}
.tee-white{background:radial-gradient(ellipse 35% 42% at 50% 50%,#dedede 0%,#e8e8e8 60%,var(--card) 100%)}
.tee-yellow{background:radial-gradient(ellipse 35% 42% at 50% 50%,#e8b512 0%,#eec64a 55%,var(--card) 100%)}
.tee-black{background:radial-gradient(ellipse 35% 42% at 50% 50%,#111 0%,#3a3a3a 55%,var(--card) 100%)}
.tee-sand{background:radial-gradient(ellipse 35% 42% at 50% 50%,#dcd2bd 0%,#e5ddcc 60%,var(--card) 100%)}

/* about */
.about-photo{left:99px;top:1404px;width:447px;height:664px;border-radius:6px;background:linear-gradient(160deg,#6b4d38 0%,#1b1716 30%,#141212 70%,#8e8a86 100%)}
.about-title{left:621px;top:1392px;font-size:38px;font-weight:600}
.about-text{left:621px;width:420px;font-size:13.5px;line-height:27px;color:#444}
.about-label{left:621px;font-size:14px;font-weight:500}
.team-title{left:621px;top:1684px;font-size:22px;font-weight:500}
.team-arrows{left:948px;top:1690px;display:flex;gap:16px}
.team-photo{left:621px;top:1741px;width:413px;height:255px;border-radius:6px;background:linear-gradient(120deg,#f5d000 0%,#e8b800 60%,#d9a400 100%)}
.about-mark{left:592px;top:1985px;font-size:68px;font-weight:500;color:var(--ink)}

/* newsletter */
.touch{left:0;top:2189px;width:1200px;height:393px;background:linear-gradient(90deg,#4f4334 0%,#8a7460 35%,#c2a58a 50%,#8a7460 65%,#3e3a33 100%)}
.touch-title{left:0;width:1200px;top:2268px;text-align:center;color:var(--white);font-size:40px;font-weight:600}
.touch-text{left:0;width:1200px;top:2344px;text-align:center;color:var(--white);font-size:19px;line-height:34px}
.touch-field{left:354px;top:2462px;width:491px;height:30px;border-bottom:1px solid rgba(255,255,255,.85);display:flex;justify-content:space-between;align-items:flex-end;padding:0 4px 6px;color:var(--white)}
.touch-field .ph{font-size:13px;opacity:.75}
.touch-field .go{font-size:12.5px;font-weight:600}

/* news */
.news-heading{left:101px;top:3185px;font-size:30px;font-weight:600}
.news{top:3255px;width:322px}
.news-img{height:200px;position:relative}
.news-date{position:absolute;left:47px;bottom:-13px;background:#2a2a2a;color:var(--white);font-size:12px;padding:9px 18px}
.news-title{margin-top:48px;font-size:21px;line-height:30px;font-weight:400}
.news-text{margin-top:14px;font-size:14px;line-height:25px;color:#777}
.news-more{margin-top:18px;font-size:13.5px;font-weight:600;display:flex;align-items:center;gap:5px}

/* footer */
.footer{left:0;top:3780px;width:1200px;height:390px;background:var(--black);color:var(--white)}
.footer .brand{color:var(--white);font-size:40px;position:absolute;left:101px;top:96px}
.socials{left:101px;top:203px;display:flex;gap:22px;align-items:center}
.social{width:36px;height:36px;border-radius:50%;border:1.5px solid var(--white)}
.social.plain{width:14px;height:14px;border:none;background:var(--white);border-radius:3px}
.divider{left:379px;top:100px;width:1px;height:175px;background:#333}
.fcol{top:95px}
.fcol h4{font-size:19px;font-weight:600;margin-bottom:16px}
.fcol li{list-style:none;font-size:14px;line-height:26px;display:flex;gap:12px;align-items:center}
.contact li{align-items:flex-start;line-height:26px;margin-bottom:10px}
.copy{left:0;width:1200px;top:322px;text-align:center;font-size:14px}
</style>
</head>
<body>

<header>
  <div class="abs search">Search the store
    <svg width="13" height="13" viewBox="0 0 13 13"><circle cx="5.5" cy="5.5" r="4" fill="none" stroke="#1f1f1f" stroke-width="2"/><line x1="8.5" y1="8.5" x2="12" y2="12" stroke="#1f1f1f" stroke-width="2"/></svg>
  </div>
  <div class="abs header-brand"><span class="brand">Bold Dawn</span></div>
  <div class="abs header-icons">
    <svg width="18" height="20" viewBox="0 0 18 20"><circle cx="9" cy="6" r="5" fill="#555"/><path d="M0 20c0-6 4-8 9-8s9 2 9 8z" fill="#555"/></svg>
    <svg width="22" height="19" viewBox="0 0 22 19"><path d="M11 19 2 10C-1 7 0 1 6 1c2 0 4 1 5 3 1-2 3-3 5-3 6 0 7 6 4 9z" fill="#555"/></svg>
    <svg width="22" height="19" viewBox="0 0 22 19"><path d="M0 1h4l3 11h12l3-9H6" fill="none" stroke="#555" stroke-width="2.5"/><rect x="6" y="4" width="14" height="7" fill="#555"/><circle cx="9" cy="16" r="2" fill="#555"/><circle cx="18" cy="16" r="2" fill="#555"/></svg>
  </div>
  <div class="abs ship">ORDERS OVER $50 SHIP FREE!</div>
  <nav class="abs nav"><a>Home</a><a>About Us</a><a>Product</a><a>Blog</a><a>Contact Us</a></nav>
  <a class="abs login">LOG IN</a>
</header>

<section class="hero">
  <div class="abs hero-photo" role="img" aria-label="Model wearing a plain white t-shirt and light jeans beside a green plant"></div>
  <h1 class="abs hero-title">Welcome<br>to Bold Dawn<br>apparel</h1>
  <a class="abs hero-btn">SHOP T-SHIRT</a>
  <span class="abs dot-btn" style="left:104px"><svg width="8" height="10"><path d="M6 1 2 5l4 4" fill="none" stroke="#333" stroke-width="1.5"/></svg></span>
  <span class="abs dot-btn" style="left:144px"><svg width="8" height="10"><path d="M2 1l4 4-4 4" fill="none" stroke="#333" stroke-width="1.5"/></svg></span>
</section>

<section class="featured">
  <h2 class="abs section-title" style="top:902px">FEATURED PRODUCTS</h2>
  <div class="abs card" style="left:97px;top:992px"><div class="card-img tee-white" role="img" aria-label="White t-shirt"><span class="card-fav"><svg width="11" height="10" viewBox="0 0 22 19"><path d="M11 18 2 10C-1 7 0 1 6 1c2 0 4 1 5 3 1-2 3-3 5-3 6 0 7 6 4 9z" fill="none" stroke="#222" stroke-width="2.5"/></svg></span></div><div class="card-row"><span class="card-name">T-shirt</span><span class="card-price">$40</span></div><p class="card-desc">Lorem ipsum dolor sit</p></div>
  <div class="abs card" style="left:352px;top:992px"><div class="card-img tee-yellow" role="img" aria-label="Yellow t-shirt"><span class="card-fav"><svg width="11" height="10" viewBox="0 0 22 19"><path d="M11 18 2 10C-1 7 0 1 6 1c2 0 4 1 5 3 1-2 3-3 5-3 6 0 7 6 4 9z" fill="none" stroke="#222" stroke-width="2.5"/></svg></span></div><div class="card-row"><span class="card-name">T-shirt</span><span class="card-price">$40</span></div><p class="card-desc">Lorem ipsum dolor sit</p></div>
  <div class="abs card" style="left:608px;top:992px"><div class="card-img tee-black" role="img" aria-label="Black t-shirt"><span class="card-fav"><svg width="11" height="10" viewBox="0 0 22 19"><path d="M11 18 2 10C-1 7 0 1 6 1c2 0 4 1 5 3 1-2 3-3 5-3 6 0 7 6 4 9z" fill="none" stroke="#222" stroke-width="2.5"/></svg></span></div><div class="card-row"><span class="card-name">T-shirt</span><span class="card-price">$40</span></div><p class="card-desc">Lorem ipsum dolor sit</p></div>
  <div class="abs card" style="left:864px;top:992px"><div class="card-img tee-sand" role="img" aria-label="Sand-coloured t-shirt"><span class="card-fav"><svg width="11" height="10" viewBox="0 0 22 19"><path d="M11 18 2 10C-1 7 0 1 6 1c2 0 4 1 5 3 1-2 3-3 5-3 6 0 7 6 4 9z" fill="none" stroke="#222" stroke-width="2.5"/></svg></span></div><div class="card-row"><span class="card-name">T-shirt</span><span class="card-price">$40</span></div><p class="card-desc">Lorem ipsum dolor sit</p></div>
</section>

<section class="about">
  <div class="abs about-photo" role="img" aria-label="Man in a black t-shirt with hand in pocket"></div>
  <h2 class="abs about-title">About Us</h2>
  <p class="abs about-text" style="top:1470px">Lorem ipsum dolor sit amet, consectetur adipiscing elit, sed do eiusmod tempor incididunt ut</p>
  <h3 class="abs about-label" style="top:1539px">Mission</h3>
  <p class="abs about-text" style="top:1568px">Lorem ipsum dolor sit amet, consectetur adipiscing elit, sed</p>
  <h3 class="abs about-label" style="top:1607px">Values</h3>
  <p class="abs about-text" style="top:1636px">Lorem ipsum dolor sit amet, consectetur adipiscing elit, sed</p>
  <h3 class="abs team-title">Team</h3>
  <div class="abs team-arrows">
    <svg width="30" height="12"><path d="M29 6H2M7 1 2 6l5 5" fill="none" stroke="#222" stroke-width="1.8"/></svg>
    <svg width="30" height="12"><path d="M1 6h27M23 1l5 5-5 5" fill="none" stroke="#bbb" stroke-width="1.8"/></svg>
  </div>
  <div class="abs team-photo" role="img" aria-label="Team member laughing against a yellow wall"></div>
  <div class="abs about-mark">Bold Dawn</div>
</section>

<section>
  <div class="abs touch" role="img" aria-label="Woman in a white t-shirt in a softly blurred room"></div>
  <h2 class="abs touch-title">Get in Touch</h2>
  <p class="abs touch-text">Sign up for the Bold Dawn newsletter and stay up to date<br>with the latest and greatest!</p>
  <div class="abs touch-field"><span class="ph">Your Email</span><span class="go">SIGN UP</span></div>
</section>

<section class="new">
  <h2 class="abs section-title" style="top:2692px">NEW PRODUCTS</h2>
  <div class="abs card" style="left:97px;top:2782px"><div class="card-img tee-white" role="img" aria-label="White t-shirt"><span class="card-fav"><svg width="11" height="10" viewBox="0 0 22 19"><path d="M11 18 2 10C-1 7 0 1 6 1c2 0 4 1 5 3 1-2 3-3 5-3 6 0 7 6 4 9z" fill="none" stroke="#222" stroke-width="2.5"/></svg></span></div><div class="card-row"><span class="card-name">T-shirt</span><span class="card-price">$40</span></div><p class="card-desc">Lorem ipsum dolor sit</p></div>
  <div class="abs card" style="left:352px;top:2782px"><div class="card-img tee-yellow" role="img" aria-label="Yellow t-shirt"><span class="card-fav"><svg width="11" height="10" viewBox="0 0 22 19"><path d="M11 18 2 10C-1 7 0 1 6 1c2 0 4 1 5 3 1-2 3-3 5-3 6 0 7 6 4 9z" fill="none" stroke="#222" stroke-width="2.5"/></svg></span></div><div class="card-row"><span class="card-name">T-shirt</span><span class="card-price">$40</span></div><p class="card-desc">Lorem ipsum dolor sit</p></div>
  <div class="abs card" style="left:608px;top:2782px"><div class="card-img tee-black" role="img" aria-label="Black t-shirt"><span class="card-fav"><svg width="11" height="10" viewBox="0 0 22 19"><path d="M11 18 2 10C-1 7 0 1 6 1c2 0 4 1 5 3 1-2 3-3 5-3 6 0 7 6 4 9z" fill="none" stroke="#222" stroke-width="2.5"/></svg></span></div><div class="card-row"><span class="card-name">T-shirt</span><span class="card-price">$40</span></div><p class="card-desc">Lorem ipsum dolor sit</p></div>
  <div class="abs card" style="left:864px;top:2782px"><div class="card-img tee-sand" role="img" aria-label="Sand-coloured t-shirt"><span class="card-fav"><svg width="11" height="10" viewBox="0 0 22 19"><path d="M11 18 2 10C-1 7 0 1 6 1c2 0 4 1 5 3 1-2 3-3 5-3 6 0 7 6 4 9z" fill="none" stroke="#222" stroke-width="2.5"/></svg></span></div><div class="card-row"><span class="card-name">T-shirt</span><span class="card-price">$40</span></div><p class="card-desc">Lorem ipsum dolor sit</p></div>
</section>

<section class="latest">
  <h2 class="abs news-heading">LATEST NEWS</h2>
  <article class="abs news" style="left:101px"><div class="news-img" role="img" aria-label="Woman in a white tee inside a café" style="background:linear-gradient(135deg,#3a2c22,#8c7662 50%,#2e2620)"><span class="news-date">22 August,2023</span></div><h3 class="news-title">Sed ut perspiciatis unde omnis iste natus error sit volu</h3><p class="news-text">Lorem ipsum dolor sit amet, consectetur adipiscing elit, sed do eiusmod tempor</p><a class="news-more">READ MORE <svg width="13" height="13"><circle cx="6.5" cy="6.5" r="6.5" fill="#1f1f1f"/><path d="M5 3.5 8 6.5 5 9.5" fill="none" stroke="#fff" stroke-width="1.6"/></svg></a></article>
  <article class="abs news" style="left:441px"><div class="news-img" role="img" aria-label="Smiling woman in a white sweatshirt on a purple backdrop" style="background:linear-gradient(135deg,#6e3f78,#a57ab0 50%,#7a4a84)"><span class="news-date">22 August,2023</span></div><h3 class="news-title">Sed ut perspiciatis unde omnis iste natus error sit volu</h3><p class="news-text">Lorem ipsum dolor sit amet, consectetur adipiscing elit, sed do eiusmod tempor</p><a class="news-more">READ MORE <svg width="13" height="13"><circle cx="6.5" cy="6.5" r="6.5" fill="#1f1f1f"/><path d="M5 3.5 8 6.5 5 9.5" fill="none" stroke="#fff" stroke-width="1.6"/></svg></a></article>
  <article class="abs news" style="left:780px"><div class="news-img" role="img" aria-label="Couple in black t-shirts against a dark wall" style="background:linear-gradient(135deg,#1f1f1f,#4a4440 50%,#141414)"><span class="news-date">22 August,2023</span></div><h3 class="news-title">Sed ut perspiciatis unde omnis iste natus error sit volu</h3><p class="news-text">Lorem ipsum dolor sit amet, consectetur adipiscing elit, sed do eiusmod tempor</p><a class="news-more">READ MORE <svg width="13" height="13"><circle cx="6.5" cy="6.5" r="6.5" fill="#1f1f1f"/><path d="M5 3.5 8 6.5 5 9.5" fill="none" stroke="#fff" stroke-width="1.6"/></svg></a></article>
</section>

<footer class="abs footer">
  <span class="brand">Bold Dawn</span>
  <div class="abs socials"><span class="social"></span><span class="social plain"></span><span class="social plain"></span><span class="social plain"></span></div>
  <div class="abs divider"></div>
  <div class="abs fcol" style="left:421px"><h4>Quick Links</h4><ul>
    <li><svg width="10" height="8"><path d="M1 1l3 3-3 3M5 1l3 3-3 3" fill="none" stroke="#fff" stroke-width="1.3"/></svg>Home</li>
    <li><svg width="10" height="8"><path d="M1 1l3 3-3 3M5 1l3 3-3 3" fill="none" stroke="#fff" stroke-width="1.3"/></svg>About Us</li>
    <li><svg width="10" height="8"><path d="M1 1l3 3-3 3M5 1l3 3-3 3" fill="none" stroke="#fff" stroke-width="1.3"/></svg>Product</li>
    <li><svg width="10" height="8"><path d="M1 1l3 3-3 3M5 1l3 3-3 3" fill="none" stroke="#fff" stroke-width="1.3"/></svg>Blog</li>
    <li><svg width="10" height="8"><path d="M1 1l3 3-3 3M5 1l3 3-3 3" fill="none" stroke="#fff" stroke-width="1.3"/></svg>Contact Us</li></ul></div>
  <div class="abs fcol" style="left:630px"><h4>Our Company</h4><ul>
    <li><svg width="10" height="8"><path d="M1 1l3 3-3 3M5 1l3 3-3 3" fill="none" stroke="#fff" stroke-width="1.3"/></svg>Terms &amp; Conditions</li>
    <li><svg width="10" height="8"><path d="M1 1l3 3-3 3M5 1l3 3-3 3" fill="none" stroke="#fff" stroke-width="1.3"/></svg>Privacy Policy</li>
    <li><svg width="10" height="8"><path d="M1 1l3 3-3 3M5 1l3 3-3 3" fill="none" stroke="#fff" stroke-width="1.3"/></svg>About Us</li>
    <li><svg width="10" height="8"><path d="M1 1l3 3-3 3M5 1l3 3-3 3" fill="none" stroke="#fff" stroke-width="1.3"/></svg>Support</li></ul></div>
  <div class="abs fcol contact" style="left:855px"><h4>Contact us</h4><ul>
    <li><svg width="12" height="16" style="margin-top:6px"><path d="M6 15C2 9 1 7 1 5a5 5 0 0 1 10 0c0 2-1 4-5 10z" fill="#fff"/><circle cx="6" cy="5" r="2" fill="#000"/></svg><span>Lorem ipsum dolor sit<br>amet, consectetur adipiscing</span></li>
    <li><svg width="14" height="14" style="margin-top:6px"><path d="M3 1l3 3-2 2c1 2 2 3 4 4l2-2 3 3-2 2C6 13 1 8 1 3z" fill="#fff"/></svg>1+ (555) 204 7781</li>
    <li><svg width="15" height="11" style="margin-top:8px"><rect width="15" height="11" fill="#fff"/><path d="M0 0l7.5 6L15 0" fill="none" stroke="#000" stroke-width="1.3"/></svg>info@bolddawnapperal.com</li></ul></div>
  <p class="abs copy">©Copyrights 2023 Bolddawnapperal &nbsp;|&nbsp; All Rights Reserved</p>
</footer>

</body>
</html>
```